banner for website

I need a new banner for my website. My website now is. www.brightmeadowkitchen.com, but I'm changing it to Bright Meadow Table and I need a new banner. I want me to be who it's about. I am my brand. I'm Carla Whitford. So, my name needs to be prominent in the banner along with my photo, which I'm attaching. I want my photo very prominent in the banner and very large. I am attaching my two favorites.
I need the banner plain ( with out the newsletter sign up optin part), so I can use it on my newsletters, emails and letter head, as well. I would like it to be inviting. I I have a certain color scheme I use. Deep dark brown letters with blues and greens. Very earthy and psychologically grounded. I would like to keep that color scheme. In my website banner, I need a opt in to sign up for my free monthly newsletter and receive my Free Pantry Basket Planner.

I want the shopping guide to be small and pleasant looking and to say: "Sign up to receive your free pantry basket planner and monthly newsletter."

I only want my banner to say: "Bright Meadow Table" "Carla Whitford"

I would also like to have part of the banner without the sign in for the newsletter part off of it. And also one with only the "Bright Meadow Table" and one with "Bright Meadow Table" and "Carla Whitford" without the newsletter sign up part on it either.

I hope you can do this for me. I look forward to seeing your design! Sincerely, Carla
Updates

Project Deadline Extended Reason: I couldn't view the designs so I couldn't look at the ones submitted. I just now got into the website with your company's help. I don't want to be penalized because of a problem with the log in at your site. That was not my fault. Please let me know your thoughts. Added Monday, May 9, 2016

Target Market(s)

people over 40 who have bad health or who want to learn how to be a vegetarian for better health.

Number of Pages Required

1 page

Requirements
Must have
• I want the shopping guide to be small and pleasant looking and to say: "Sign up to receive your free pantry basket planner and monthly newsletter." I would like it to blend and be elegant and not in the middle of the banner or across my face.
• I only want my banner to say: "Bright Meadow Table" "Carla Whitford"
• I would also like to have part of the banner without the sign in for the newsletter part off of it. And also one with only the "Bright Meadow Table" and one with "Bright Meadow Table" and "Carla Whitford" without the newsletter sign up part on it either.
Nice to have
• Nice font and colors. I want the background to be plants and earthy and inviting.
Should not have
• I updated and added two new photos. I think the one you were using with me in the red top looked funny under my eyes. it was too pink or something. I uploaded a better version of that photo. in hopes that it looks better. Please switch those out if you are using the one with me in the red top.

```html
<!DOCTYPE html>
<html lang="en">
<head>
<meta charset="utf-8">
<title>Carla Whitford – Bright Meadow Table Banner</title>
<link rel="stylesheet" href="https://fonts.googleapis.com/css2?family=Roboto:wght@400&family=Raleway:wght@500&display=swap">
<style>
  :root {
    --forest-deep: #1f4a12;
    --forest-mid: #4f8a1c;
    --forest-light: #a9cf3a;
    --forest-glow: #e6f2a0;
    --deck-dark: #3a2a20;
    --deck-mid: #5e4638;
    --deck-light: #7a6254;
    --bar-bg: rgba(28, 28, 28, 0.85);
    --text-light: #ffffff;
    --accent-orange: #f29c11;
    --portrait-light: #e3ecc4;
    --portrait-mid: #c9c09a;
  }

  * { box-sizing: border-box; margin: 0; padding: 0; }

  html, body {
    width: 1200px;
    height: 510px;
    overflow: hidden;
    background: #ffffff;
  }

  .banner {
    position: relative;
    width: 1200px;
    height: 510px;
    overflow: hidden;
    font-family: "Roboto", Arial, sans-serif;
  }

  .banner__scene {
    position: absolute;
    inset: 0;
    background:
      linear-gradient(180deg,
        var(--deck-light) 0%, var(--deck-mid) 40%, var(--deck-dark) 100%) 0 398px / 100% 112px no-repeat,
      radial-gradient(ellipse 260px 200px at 700px 20px, var(--forest-glow) 0%, rgba(230,242,160,0) 100%),
      linear-gradient(90deg,
        var(--forest-deep) 0%, var(--forest-mid) 20%, var(--forest-light) 48%,
        var(--forest-mid) 75%, var(--forest-deep) 100%);
  }

  .banner__portrait {
    position: absolute;
    left: 87px;
    top: 38px;
    width: 392px;
    height: 392px;
    border-radius: 50%;
    border: 5px solid var(--text-light);
    background: linear-gradient(135deg, var(--portrait-light) 0%, var(--portrait-mid) 100%);
  }

  .banner__title {
    position: absolute;
    left: 528px;
    top: 172px;
    color: var(--text-light);
    font-weight: 400;
    text-transform: uppercase;
    line-height: 1;
  }

  .banner__name {
    display: block;
    font-size: 62px;
    letter-spacing: 2px;
  }

  .banner__brand {
    display: block;
    margin-top: 12px;
    font-size: 45px;
    letter-spacing: 0.5px;
  }

  .signup-bar {
    position: absolute;
    left: 0;
    top: 460px;
    width: 1200px;
    height: 50px;
    background: var(--bar-bg);
  }

  .signup-bar__text {
    position: absolute;
    left: 95px;
    top: 12px;
    color: var(--text-light);
    font-family: "Raleway", Arial, sans-serif;
    font-weight: 500;
    font-size: 22px;
    line-height: 26px;
    white-space: nowrap;
  }

  .signup-bar__button {
    position: absolute;
    left: 985px;
    top: 7px;
    width: 105px;
    height: 33px;
    background: var(--accent-orange);
    color: var(--text-light);
    font-family: "Roboto", Arial, sans-serif;
    font-size: 16px;
    letter-spacing: 0.3px;
    display: flex;
    align-items: center;
    justify-content: center;
    text-decoration: none;
  }
</style>
</head>
<body>
  <header class="banner">
    <div class="banner__scene" role="img" aria-label="Sunlit green forest photograph above a weathered wooden deck"></div>

    <div class="banner__portrait" role="img" aria-label="Portrait photograph of Carla Whitford"></div>

    <h1 class="banner__title">
      <span class="banner__name">Carla Whitford</span>
      <span class="banner__brand">Bright Meadow Table</span>
    </h1>

    <div class="signup-bar">
      <p class="signup-bar__text">Sign up for my free monthly newsletter and receive my free pantry basket planner</p>
      <a class="signup-bar__button" href="#signup">SIGN UP</a>
    </div>
  </header>
</body>
</html>
```